Locksmith Business Cards

My father-in-law is in need of new business cards for his locksmith business and I need to impress him. Kindly help me out!

You can see the previous business card attached. It is a family run business in North Wales.

No individual names on the cards.

Key Things to Feature:
- The words "Prompt", "Local", "Reliable" (as you can see under the logo on the website)
- 24h Emergency Service
- Covering All of North Wales, the Wirral and Chester
- The color blue
- A key or a lock would be interesting (similar to the ones that come up when you google locksmith business card)

Optional (only if design includes bullet points, like the example below):
https://imgvaultcdn.net/samples/208314/55172/55172_3904821_208314_image.jpg
- Residential / Commercial / Automotive
- Alarms & Cameras
- Key Cutting & Safes

https://www.brynhafod-locksmiths.co.uk/

Industry/Entity Type

Locksmith

Contact Information for Business Card

01632 960 418
07700 900 362
brynhafodlocksmiths@mailvane.com
Brynhafod Locksmiths, The Willow Barn, 7 Tannery Rd., Llandudno LL99 4QX
www.brynhafod-locksmiths.co.uk

Requirements
Must have
• - The words "Prompt", "Local", "Reliable" (as you can see under the logo on the website)
• - 24h Emergency Service
• - Covering All of North Wales, the Wirral and Chester
Nice to have
• - A key or a lock would be interesting (similar to the ones that come up when you google locksmith business card)

```html
<!DOCTYPE html>
<html lang="en">
<head>
<meta charset="utf-8">
<title>Brynhafod Locksmiths – Business Card</title>
<link rel="stylesheet" href="https://fonts.googleapis.com/css2?family=Oswald:wght@300;400&family=Montserrat:wght@500&display=swap">
<style>
  :root {
    --page-bg: #e9e6e1;
    --card-white: #f7f7f8;
    --navy: #252c6e;
    --band-blue: #262f7b;
    --accent-blue: #1f8fd3;
    --divider-grey: #c9cbd2;
    --text-light: #eef0f8;
    --icon-blue: #2c8ed0;
  }
  * { margin: 0; padding: 0; box-sizing: border-box; }
  html, body {
    width: 1200px;
    height: 1054px;
    overflow: hidden;
    background: var(--page-bg);
  }
  .business-card {
    position: absolute;
    left: 100px;
    top: 227px;
    width: 1000px;
    height: 600px;
    background: var(--card-white);
    box-shadow: 0 10px 30px rgba(0,0,0,0.12);
    overflow: hidden;
  }
  .brand-header {
    position: absolute;
    left: 94px;
    top: 57px;
    display: flex;
    align-items: center;
    gap: 26px;
  }
  .brand-square {
    width: 108px;
    height: 108px;
    border-radius: 18px;
    background: var(--navy);
    flex: none;
  }
  .brand-text { display: flex; flex-direction: column; }
  .brand-name {
    font-family: "Oswald", sans-serif;
    font-weight: 400;
    font-size: 70px;
    line-height: 1;
    letter-spacing: 0.01em;
    color: var(--navy);
    text-transform: uppercase;
  }
  .brand-tagline {
    margin-top: 12px;
    font-family: "Montserrat", sans-serif;
    font-weight: 500;
    font-size: 25px;
    letter-spacing: 0.2em;
    color: var(--navy);
    white-space: nowrap;
  }
  .brand-tagline .sep { margin: 0 14px; }
  .divider-line {
    position: absolute;
    left: 0; right: 0;
    top: 240px;
    height: 6px;
    background: var(--divider-grey);
  }
  .info-band {
    position: absolute;
    left: 0; right: 0;
    top: 246px;
    height: 272px;
    background: var(--band-blue);
  }
  .service-info {
    position: absolute;
    left: 98px;
    top: 74px;
    width: 380px;
    font-family: "Oswald", sans-serif;
  }
  .service-title {
    font-weight: 400;
    font-size: 36px;
    line-height: 1.1;
    color: var(--accent-blue);
    white-space: nowrap;
  }
  .service-area {
    margin-top: 8px;
    font-weight: 400;
    font-size: 24px;
    line-height: 1.3;
    color: var(--text-light);
  }
  .contact-list {
    position: absolute;
    left: 512px;
    top: 56px;
    list-style: none;
    font-family: "Oswald", sans-serif;
    font-weight: 400;
    font-size: 27px;
    color: var(--text-light);
  }
  .contact-list li {
    display: flex;
    align-items: center;
    height: 40.5px;
    white-space: nowrap;
  }
  .contact-icon {
    width: 22px;
    height: 22px;
    margin-right: 24px;
    flex: none;
  }
  .address-strip {
    position: absolute;
    left: 0; right: 0;
    top: 518px;
    height: 82px;
    display: flex;
    align-items: center;
    justify-content: center;
    font-family: "Oswald", sans-serif;
    font-weight: 400;
    font-size: 27px;
    color: var(--navy);
  }
</style>
</head>
<body>
  <main class="business-card">
    <header class="brand-header">
      <div class="brand-square"></div>
      <div class="brand-text">
        <h1 class="brand-name">Brynhafod Locksmiths</h1>
        <p class="brand-tagline">PROMPT<span class="sep">|</span>LOCAL<span class="sep">|</span>RELIABLE</p>
      </div>
    </header>

    <div class="divider-line"></div>

    <section class="info-band">
      <div class="service-info">
        <p class="service-title">24h Emergency Service</p>
        <p class="service-area">Covering All of North Wales,<br>the Wirral and Chester</p>
      </div>

      <ul class="contact-list">
        <li>
          <svg class="contact-icon" viewBox="0 0 24 24" aria-hidden="true"><path fill="var(--icon-blue)" d="M3 8c0-2 3-4 9-4s9 2 9 4v2h-5V8H8v2H3zM6 11h12l2 8H4zM12 13a2.5 2.5 0 1 0 0 5a2.5 2.5 0 1 0 0-5z"/></svg>
          01632 960 418
        </li>
        <li>
          <svg class="contact-icon" viewBox="0 0 24 24" aria-hidden="true"><path fill="var(--icon-blue)" d="M3 8c0-2 3-4 9-4s9 2 9 4v2h-5V8H8v2H3zM6 11h12l2 8H4zM12 13a2.5 2.5 0 1 0 0 5a2.5 2.5 0 1 0 0-5z"/></svg>
          07700 900 362
        </li>
        <li>
          <svg class="contact-icon" viewBox="0 0 24 24" aria-hidden="true"><rect x="2" y="5" width="20" height="14" fill="var(--icon-blue)"/><path d="M2 5l10 8l10-8" fill="none" stroke="var(--band-blue)" stroke-width="2"/></svg>
          brynhafodlocksmiths@mailvane.com
        </li>
        <li>
          <svg class="contact-icon" viewBox="0 0 24 24" aria-hidden="true"><g fill="none" stroke="var(--icon-blue)" stroke-width="2"><circle cx="12" cy="12" r="9"/><ellipse cx="12" cy="12" rx="4" ry="9"/><path d="M3 12h18M5 7h14M5 17h14"/></g></svg>
          www.brynhafod-locksmiths.co.uk
        </li>
      </ul>
    </section>

    <footer class="address-strip">
      The Willow Barn, 7 Tannery Rd., Llandudno LL99 4QX
    </footer>
  </main>
</body>
</html>
```